Maplecrest Disability - Social Security Disability Attorneys

Our company is expanding to attract clients nationwide for our social security disability practice. We have a logo, but I am looking for a creative and elegant letterhead that projects an image of being technologically advanced but still professional enough for the legal field. I am looking for the "wow factor" combined with this is still professional enough for a law practice.

Requesting letterhead and business card design
Updates

Had to update and change the logo. The previous logo had a typo. Please send updates with the new logo for consideration. The letterhead and business cards should be professional enough to be used for a law firm. Thanks.

Industry/Entity Type

Law Practice, Law Firm, Healthcare Industry, Government

Colors

Designer to choose colors to be used in the design.

Requirements
Nice to have
• **Please create a vertical design for the business card**

```html
<!DOCTYPE html>
<html lang="en">
<head>
<meta charset="utf-8">
<title>Maplecrest Disability – Letterhead</title>
<link rel="stylesheet" href="https://fonts.googleapis.com/css2?family=Lato:wght@400;700&family=Dancing+Script:wght@500&display=swap">
<style>
  :root {
    --backdrop: #e9e9ea;
    --paper: #ffffff;
    --ink: #2b2b2b;
    --ink-soft: #444444;
    --accent: #f0842a;
  }
  * { box-sizing: border-box; margin: 0; padding: 0; }
  html, body {
    width: 1200px; height: 960px; overflow: hidden;
    background: var(--backdrop);
  }
  .canvas {
    width: 1200px; height: 960px;
    display: flex; align-items: center; justify-content: center;
  }
  .letterhead {
    position: relative;
    width: 636px; height: 900px;
    background: var(--paper);
    box-shadow: 0 6px 22px rgba(0,0,0,.12);
    font-family: "Lato", sans-serif;
    color: var(--ink);
    padding: 64px 58px 0 62px;
  }
  .brand {
    display: flex; align-items: center; gap: 9px;
  }
  .brand-dot {
    width: 14px; height: 14px; border-radius: 50%;
    background: var(--accent);
  }
  .brand-name {
    font-size: 19px; font-weight: 700; color: var(--ink);
  }
  .letter-date { margin-top: 74px; font-size: 12px; }
  .recipient { margin-top: 16px; font-size: 12px; line-height: 1.3; font-style: normal; }
  .recipient-company { margin-top: 14px; }
  .salutation { margin-top: 16px; font-size: 14px; font-weight: 700; }
  .letter-body p {
    margin-top: 14px; font-size: 11px; line-height: 1.42; color: var(--ink-soft);
  }
  .letter-body p:first-child { margin-top: 12px; }
  .closing { margin-top: 34px; font-size: 12px; color: var(--ink-soft); }
  .signature {
    margin-top: 6px; font-family: "Dancing Script", cursive;
    font-size: 40px; color: var(--ink);
  }
  .contact-bar {
    position: absolute; left: 62px; right: 40px; bottom: 66px;
    font-size: 10px; color: var(--ink);
    display: flex; flex-direction: column; align-items: flex-end;
  }
  .contact-row { display: flex; align-items: center; gap: 12px; white-space: nowrap; }
  .contact-item { display: flex; align-items: center; gap: 5px; white-space: nowrap; }
  .contact-icon {
    flex: none;
    width: 16px; height: 13px; background: var(--accent);
    display: flex; align-items: center; justify-content: center;
  }
  .contact-address { margin-top: 7px; white-space: nowrap; padding-right: 60px; }
</style>
</head>
<body>
<div class="canvas">
  <article class="letterhead">
    <header class="brand">
      <span class="brand-dot"></span>
      <span class="brand-name">Maplecrest Disability</span>
    </header>

    <p class="letter-date">January-03-2020</p>

    <address class="recipient">
      <div>Mr. Daniel Reyes</div>
      <div>President</div>
      <div class="recipient-company">Northfield Partners</div>
      <div>48 Harbor Lane, Suite# 10</div>
      <div>Rivertown, State, 120023</div>
    </address>

    <p class="salutation">Dear Mr. Daniel</p>

    <section class="letter-body">
      <p>Lorem ipsum dolor sit amet, consectetur adipisicing elit, sed do eiusmod tempor incididunt ut labore et dolore magna aliqua. Ut enim ad minim veniam, quis nostrud exercitation ullamco laboris nisi ut aliquip ex ea commodo consequat. Duis aute irure dolor in reprehenderit in voluptate velit esse cillum dolore eu fugiat nulla pariatur.</p>
      <p>Lorem ipsum dolor sit amet, consectetur adipisicing elit, sed do eiusmod tempor incididunt ut labore et dolore magna aliqua. Ut enim ad minim veniam, quis nostrud exercitation ullamco laboris nisi ut aliquip ex ea commodo consequat. Duis aute irure dolor in reprehenderit in voluptate velit esse cillum dolore eu fugiat nulla pariatur.</p>
      <p>Lorem ipsum dolor sit amet, consectetur adipisicing elit, sed do eiusmod tempor incididunt ut labore et dolore magna aliqua. Ut enim ad minim veniam, quis nostrud exercitation ullamco laboris nisi ut aliquip ex ea commodo consequat.</p>
      <p>Excepteur sint occaecat cupidatat non proident, sunt in culpa qui officia deserunt mollit anim id est laborum. re et dolore magnam aliquam quaerat voluptatem.</p>
    </section>

    <p class="closing">Regards</p>
    <p class="signature">Laura Bennett</p>

    <footer class="contact-bar">
      <div class="contact-row">
        <span class="contact-item">
          <span class="contact-icon">
            <svg width="9" height="9" viewBox="0 0 10 10" aria-hidden="true"><path d="M2 1l2 2-1 1.3c.6 1.2 1.5 2.1 2.7 2.7L7 6l2 2-1.2 1.2C4.5 9 1 5.5.8 2.2z" fill="#fff"/></svg>
          </span>555-214-7390
        </span>
        <span class="contact-item">
          <span class="contact-icon">
            <svg width="10" height="8" viewBox="0 0 10 8" aria-hidden="true"><rect x=".5" y=".5" width="9" height="7" fill="none" stroke="#fff"/><path d="M.5.5L5 4.5 9.5.5" fill="none" stroke="#fff"/></svg>
          </span>info@maplecrestdisability.com
        </span>
        <span class="contact-item">
          <span class="contact-icon">
            <svg width="9" height="9" viewBox="0 0 10 10" aria-hidden="true"><circle cx="5" cy="5" r="4.3" fill="none" stroke="#fff"/><ellipse cx="5" cy="5" rx="1.8" ry="4.3" fill="none" stroke="#fff"/><path d="M.7 5h8.6" stroke="#fff"/></svg>
          </span>www.maplecrestdisability.com
        </span>
      </div>
      <div class="contact-address">Suite 4, Level 12, Kingsway Road Brookfield 2041</div>
    </footer>
  </article>
</div>
</body>
</html>
```